New word press website site design

We provide email marketing to aircraft brokers and dealers to assist in finding buyers for their aircraft.

Our target market to purchase our broadcasts are the aircraft sellers – NOT the buyers.

Our target market when sending the email broadcast, are the buyers (end users).

The website should target brokers and our email database targets the buyers.

We do not buy or sell aircraft as a company. We provide email marketing solutions to connect buyers and sellers of aircraft.

Our other site is planelantern.com and will be redesigned soon. Please use it as a reference as far as general scope but they layout can be completely different and should include helicopters only as far as imagery. The colors should be similar as the logos are similar, however we do NOT want both sites to be identical in use of primary color

Plenty of images and sample broadcasts attached to use as needed throughout the site.

Headlines listed below with some text copy.

In the event that we need to add more text, please use standard greek text as a place holder for the purposes of the mockup design.

Need to have a “SUBSCRIBE” button to join our mailing list.

Possible Headlines:

Exclusively Showcasing Rotor Wing Aircraft to the Global Marketplace

Showcasing Pre-Owned Helicopters Available For Sale, Lease, Trade, or Wanted for Acquisition.

Mobile-optimized Email Campaigns that Render Correctly Across all Devices

Targeted worldwide recipients that currently own, operate, or have an interest in rotor wing aircraft

STRONGEST Rotor Wing Database in the Industry

Text/Copy:

HOME
Rotorbay Vista is one of most powerful marketing tools in the industry to utilize in reaching targeted buyers of pre-owned helicopters. Rotorbay Vista provides the rotor wing aircraft market with a fast, effective, and affordable email broadcast solution to utilize in the marketing of Helicopters for sale.

Developed Exclusively to Showcase Rotor Wing Aircraft to the Global marketplace, Rotorbay Vista is a powerful tool designed to maximize leads and accelerate the sales process by providing the ability to reach a global network of Helicopter buyers in a matter of seconds.

DATABASE:

While Rotorbay Vista is delivered to all known broker/dealers, our primary focus is in reaching end users. Our opt-in/opt-out recipient database is updated daily and developed specifically to deliver the latest details on helicopters available for sale or lease to the inboxes of a global network of Helicopter buyers and sellers.

· Helicopter Owners

· Helicopter Operators

· Helicopter Charter Services

· Helicopter Management Companies

· Corporate/Municipal Flight Departments

· Helicopter Pilots

· Senior Aviation Executives

· Wealth Management Firms

· High Net Worth Individuals

· Helicopter Broker/Dealers

Helicopter Tour/Travel Firms

· Off Shore Oil & Gas Production Firms

· Municipalities/Media/Medevac Firms

Our recipient database is continuously updated and developed specifically to reach buyers and sellers of Helicopters. This ensures that your Helicopter will be showcased to the right people. Rotorbay Vista does not broadcast non-rotor wing aircraft and focuses exclusively on the Global Helicopter Market.

Broadcast Design:

Rotorbay Vista broadcast ads are custom designed for you by incorporating your corporate image and branding. Because you have worked hard in developing your corporate image, we strive to maintain it while designing an ad that will showcase your Helicopter to its best advantage. Rotorbay Vista utilizes Mobile-optimized Email Campaigns with Responsive Coding to render correctly across all devices

Once you have approved the design, we schedule the broadcast to be sent on the available date and time you request. The broadcast will link to your website and the results can be immediate. All email leads and replies will go to the email address that you provided.

Pricing:
Create a place holder for 3 Different Broadcast Packages

-Broadcast Package A
-Broadcast Package B
-Broadcast Package C

Target Market(s)

The target market is any person or company that has aircraft for sale. We work with brokers, dealers, and owners to assist in finding buyers for their aircraft using email marketing campaigns (Showcase broadcasts).

Industry/Entity Type

Aviation

Colors
0255a3
00a990

Requirements
Nice to have
• Samples of helicopter for sale broadcast ads in /image gallery/slider

```html
<!DOCTYPE html>
<html lang="en">
<head>
<meta charset="utf-8">
<title>Rotorbay Vista — Rotor Wing Email Broadcasts</title>
<link rel="stylesheet" href="https://fonts.googleapis.com/css2?family=Lato:wght@400;700;900&display=swap">
<style>
  :root {
    --red: #d0000b;
    --red-deep: #9e0008;
    --ink: #141414;
    --text: #222222;
    --white: #ffffff;
    --mist: #e4e4e4;
    --night: #1c1c1e;
  }
  * { box-sizing: border-box; margin: 0; padding: 0; }
  html, body { width: 695px; height: 1200px; overflow: hidden; }
  body { font-family: "Lato", Arial, sans-serif; color: var(--text); background: var(--white); }
  .page { position: relative; width: 695px; height: 1200px; overflow: hidden; }

  /* Hero */
  .hero { position: absolute; left: 0; top: 0; width: 695px; height: 315px; border-top: 3px solid var(--red); }
  .hero-photo { position: absolute; inset: 0; background: radial-gradient(ellipse at 45% 40%, #3a3a3e 0%, #232326 45%, #111112 100%); }
  .brand-tab {
    position: absolute; left: 213px; top: 0; width: 269px; height: 50px;
    background: var(--red); border-radius: 0 0 24px 24px;
    display: flex; align-items: center; justify-content: center;
  }
  .brand-name { color: var(--white); font-weight: 700; font-size: 23px; letter-spacing: 0.2px; }
  .hero-title {
    position: absolute; left: 0; top: 139px; width: 695px; text-align: center;
    color: var(--white); font-weight: 700; font-size: 20px; line-height: 27px;
  }
  .btn {
    display: inline-flex; align-items: center; justify-content: center;
    border-radius: 14px; font-weight: 700; text-transform: uppercase; color: var(--white);
    text-decoration: none;
  }
  .btn-subscribe { position: absolute; left: 287px; top: 209px; width: 134px; height: 29px; background: var(--red); font-size: 11px; }

  /* Intro band */
  .intro { position: absolute; left: 0; top: 315px; width: 695px; height: 211px; }
  .intro-photo { position: absolute; inset: 0; background: linear-gradient(160deg, #c8000a 0%, #b80008 50%, #cf000b 100%); }
  .intro-copy { position: absolute; left: 110px; top: 55px; width: 475px; text-align: center; color: var(--white); font-size: 9.3px; line-height: 15px; }
  .intro-copy p + p { margin-top: 14px; padding: 0 35px; }

  /* Database */
  .database { position: absolute; left: 0; top: 526px; width: 695px; height: 304px; background: var(--white); }
  .database-photo { position: absolute; left: 0; top: 0; width: 289px; height: 304px; background: linear-gradient(180deg, #4d5d86 0%, #7a6c82 50%, #3a3a3a 75%, #555652 100%); }
  .database-title { position: absolute; left: 301px; top: 27px; font-size: 16px; font-weight: 400; color: var(--ink); }
  .database-text { position: absolute; left: 302px; top: 57px; width: 376px; font-size: 9.6px; line-height: 15px; color: var(--ink); }
  .audience { position: absolute; top: 137px; list-style: none; font-size: 8.1px; color: var(--ink); }
  .audience li { height: 18.6px; display: flex; align-items: center; }
  .audience svg { width: 8px; height: 8px; margin-right: 11px; flex: none; }
  .audience-left { left: 301px; }
  .audience-right { left: 490px; }

  /* Pricing */
  .pricing { position: absolute; left: 0; top: 830px; width: 695px; height: 330px; }
  .pricing-photo { position: absolute; inset: 0; background: linear-gradient(180deg, #d6d6d6 0%, #ececec 45%, #e2e2e2 75%, #cfcfcf 100%); }
  .pricing-title { position: absolute; left: 0; top: 52px; width: 695px; text-align: center; font-size: 15px; font-weight: 700; color: var(--ink); }
  .plan { position: absolute; top: 106px; width: 208px; height: 168px; filter: drop-shadow(0 4px 8px rgba(0,0,0,0.28)); }
  .plan-shape { position: absolute; inset: 0; width: 208px; height: 168px; }
  .plan-a { left: 12px; }
  .plan-b { left: 240px; }
  .plan-c { left: 467px; }
  .plan-name { position: absolute; left: 12px; top: 15px; font-size: 18px; line-height: 21px; font-weight: 400; color: var(--ink); }
  .plan-price { position: absolute; left: 117px; top: 28px; font-size: 15.5px; font-weight: 700; color: var(--red); }
  .plan-desc { position: absolute; left: 15px; top: 73px; width: 160px; font-size: 9px; line-height: 14px; color: var(--ink); }
  .btn-order { position: absolute; left: 15px; top: 113px; width: 92px; height: 21px; font-size: 8.5px; border-radius: 11px; background: var(--red); }
  .plan-a .plan-name, .plan-a .plan-price, .plan-a .plan-desc { color: var(--white); }
  .plan-a .btn-order { background: var(--ink); }

  /* Footer */
  .footer { position: absolute; left: 0; top: 1160px; width: 695px; height: 40px; background: var(--white); display: flex; align-items: center; justify-content: center; font-size: 9px; color: var(--ink); }
</style>
</head>
<body>
<div class="page">

  <header class="hero">
    <div class="hero-photo" role="img" aria-label="Photo of a helicopter silhouetted on an airfield at dusk"></div>
    <div class="brand-tab"><span class="brand-name">Rotorcast Media Inc</span></div>
    <h1 class="hero-title">Exclusively Showcasing Rotor Wing Aircraft<br>to the Global Marketplace</h1>
    <a class="btn btn-subscribe" href="#">Subscribe</a>
  </header>

  <section class="intro">
    <div class="intro-photo" role="img" aria-label="Red-tinted photo of a helicopter in the background"></div>
    <div class="intro-copy">
      <p>While Rotorbay Vista is delivered to all known broker/dealers, our primary focus is in reaching end users. Our opt-in/opt-out recipient database is updated daily and developed specifically to deliver the latest details on helicopters available for sale or lease to the inboxes of a global network of Helicopter buyers and sellers.</p>
      <p>Developed Exclusively to Showcase Rotor Wing Aircraft to the Global marketplace, Rotorbay Vista is a powerful tool designed to maximize leads and accelerate the sales process by providing the ability to reach a global network of Helicopter buyers in a matter of seconds.</p>
    </div>
  </section>

  <section class="database">
    <div class="database-photo" role="img" aria-label="Photo of a black helicopter parked on a helipad at sunset"></div>
    <h2 class="database-title">Database</h2>
    <p class="database-text">While Rotorbay Vista is delivered to all known broker/dealers, our primary focus is in reaching end users. Our opt-in/opt-out recipient database is updated daily and developed specifically to deliver the latest details on helicopters available for sale or lease to the in boxes of a global network of Helicopter buyers and sellers.</p>
    <svg width="0" height="0" style="position:absolute">
      <symbol id="tick" viewBox="0 0 10 10"><path d="M1 5.2 L3.8 8 L9 2" fill="none" stroke="#d0000b" stroke-width="2.2"/></symbol>
    </svg>
    <ul class="audience audience-left">
      <li><svg><use href="#tick"/></svg>Helicopter Owners</li>
      <li><svg><use href="#tick"/></svg>Helicopter Operators</li>
      <li><svg><use href="#tick"/></svg>Helicopter Charter Services</li>
      <li><svg><use href="#tick"/></svg>Helicopter Management Companies</li>
      <li><svg><use href="#tick"/></svg>Corporate/Municipal Flight Departments</li>
      <li><svg><use href="#tick"/></svg>Helicopter Pilots</li>
      <li><svg><use href="#tick"/></svg>Senior Aviation Executives</li>
    </ul>
    <ul class="audience audience-right">
      <li><svg><use href="#tick"/></svg>Helicopter Broker/Dealers</li>
      <li><svg><use href="#tick"/></svg>Helicopter Tour/Travel Firms</li>
      <li><svg><use href="#tick"/></svg>Off Shore Oil &amp; Gas Production Firms</li>
      <li><svg><use href="#tick"/></svg>Municipalities/Media/Medevac Firms</li>
      <li><svg><use href="#tick"/></svg>Wealth Management Firms</li>
      <li><svg><use href="#tick"/></svg>High Net Worth Individuals</li>
    </ul>
  </section>

  <section class="pricing">
    <div class="pricing-photo" role="img" aria-label="Faded grey photo of helicopters in flight"></div>
    <h2 class="pricing-title">Pricing</h2>

    <article class="plan plan-a">
      <svg class="plan-shape" viewBox="0 0 208 168" aria-hidden="true">
        <polygon points="0,0 208,0 184,168 0,168" fill="#d0000b"/>
        <polygon points="160,168 196.6,80 184,168" fill="#141414"/>
      </svg>
      <h3 class="plan-name">Broadcast<br>Package A</h3>
      <span class="plan-price">$100.00</span>
      <p class="plan-desc">Neque porro quisquam est qui dolorem ipsum quia dolor sit amet</p>
      <a class="btn btn-order" href="#">Order Now</a>
    </article>

    <article class="plan plan-b">
      <svg class="plan-shape" viewBox="0 0 208 168" aria-hidden="true">
        <polygon points="0,0 208,0 184,168 0,168" fill="#ffffff"/>
        <polygon points="160,168 196.6,80 184,168" fill="#d0000b"/>
      </svg>
      <h3 class="plan-name">Broadcast<br>Package B</h3>
      <span class="plan-price">$100.00</span>
      <p class="plan-desc">Neque porro quisquam est qui dolorem ipsum quia dolor sit amet</p>
      <a class="btn btn-order" href="#">Order Now</a>
    </article>

    <article class="plan plan-c">
      <svg class="plan-shape" viewBox="0 0 208 168" aria-hidden="true">
        <polygon points="0,0 208,0 184,168 0,168" fill="#ffffff"/>
        <polygon points="160,168 196.6,80 184,168" fill="#d0000b"/>
      </svg>
      <h3 class="plan-name">Broadcast<br>Package c</h3>
      <span class="plan-price">$100.00</span>
      <p class="plan-desc">Neque porro quisquam est qui dolorem ipsum quia dolor sit amet</p>
      <a class="btn btn-order" href="#">Order Now</a>
    </article>
  </section>

  <footer class="footer">©2018 Company&nbsp; Name&nbsp; |&nbsp; All RIghts Reserved</footer>

</div>
</body>
</html>
```